Business cards and stationary design

We just completed the design of our new logo and we need to print new business cards and letterhead for our nonprofit. We are looking for a fresh new design that shows off our new logo. On letterhead, we must have a column on the right or left to include our Board of Directors (up to 45 names) (see attachment)

Industry/Entity Type

Non-Profit

Contact Information for Business Card

Standard business card with name, title, Company name, mailing address phone numbers, email address and website. Tagline on back "Bringing the homeless home"

Font styles to use
Sans Serif

Requirements
Must have
• include pertinent information above
• new logo
• fonts compatible with logo
• should use logo colors only
Nice to have
• tag lines

```html
<!DOCTYPE html>
<html lang="en">
<head>
<meta charset="utf-8">
<title>Harbor Shelter Alliance – Business Card</title>
<link rel="stylesheet" href="https://fonts.googleapis.com/css2?family=Roboto:wght@400;500;700&family=Roboto+Condensed:wght@500;700&display=swap">
<style>
  :root {
    --backdrop: #2a2a2a;
    --brand-red: #d62027;
    --brand-teal: #0a84a3;
    --card-white: #f1f1f1;
    --text-grey: #555555;
    --white: #ffffff;
  }
  html, body {
    margin: 0;
    padding: 0;
    width: 1200px;
    height: 960px;
    overflow: hidden;
    background: var(--backdrop);
    font-family: "Roboto", sans-serif;
  }
  .canvas {
    position: relative;
    width: 1200px;
    height: 960px;
  }
  .card {
    position: absolute;
    left: 320px;
    width: 600px;
    height: 342px;
    box-sizing: border-box;
  }
  /* Front of card */
  .card-front {
    top: 105px;
    background: var(--brand-red);
  }
  .front-brand {
    position: absolute;
    left: 0;
    right: 0;
    top: 150px;
    display: flex;
    justify-content: center;
    align-items: center;
    gap: 14px;
    color: var(--white);
    font-weight: 500;
    font-size: 34px;
  }
  .brand-square {
    width: 26px;
    height: 26px;
    background: currentColor;
  }
  .front-website {
    position: absolute;
    left: 0;
    right: 0;
    top: 294px;
    text-align: center;
    color: var(--white);
    font-size: 15px;
    letter-spacing: 5.2px;
  }
  /* Back of card */
  .card-back {
    top: 493px;
    background: var(--card-white);
  }
  .back-brand {
    position: absolute;
    left: 36px;
    top: 96px;
    display: flex;
    align-items: center;
    gap: 10px;
    color: var(--brand-teal);
    font-weight: 500;
    font-size: 21px;
    letter-spacing: 0.5px;
  }
  .back-brand .brand-square {
    width: 18px;
    height: 18px;
  }
  .address {
    position: absolute;
    left: 37px;
    top: 183px;
    margin: 0;
    font-style: normal;
    color: var(--text-grey);
    font-size: 14px;
    line-height: 18px;
  }
  .address .org-name {
    font-weight: 700;
  }
  .contact-list {
    position: absolute;
    left: 37px;
    top: 252px;
    margin: 0;
    padding: 0;
    list-style: none;
    color: var(--text-grey);
    font-size: 14px;
    line-height: 19px;
  }
  .contact-list li {
    display: flex;
    align-items: center;
    gap: 8px;
  }
  .contact-list svg {
    width: 13px;
    height: 13px;
    fill: var(--brand-teal);
  }
  .name-band {
    position: absolute;
    left: 360px;
    top: 230px;
    width: 240px;
    height: 64px;
  }
  .name-band svg {
    position: absolute;
    inset: 0;
  }
  .name-band .person {
    position: absolute;
    right: 31px;
    top: 7px;
    text-align: right;
    color: var(--white);
    font-family: "Roboto Condensed", sans-serif;
  }
  .person .person-name {
    display: block;
    font-weight: 700;
    font-size: 23px;
    line-height: 26px;
  }
  .person .person-title {
    display: block;
    font-weight: 500;
    font-size: 15px;
    line-height: 20px;
  }
</style>
</head>
<body>
<main class="canvas">
  <section class="card card-front" aria-label="Card front">
    <div class="front-brand">
      <span class="brand-square"></span>
      <span class="brand-name">Harbor Shelter Alliance</span>
    </div>
    <div class="front-website">www.harborshelter.org</div>
  </section>

  <section class="card card-back" aria-label="Card back">
    <div class="back-brand">
      <span class="brand-square"></span>
      <span class="brand-name">Harbor Shelter Alliance</span>
    </div>

    <address class="address">
      <span class="org-name">Harbor Shelter Alliance</span><br>
      412 Birchwood Road<br>
      Juneau, Alaska 99801
    </address>

    <ul class="contact-list">
      <li>
        <svg viewBox="0 0 16 16" aria-hidden="true"><path d="M3.6 1.2 6 3.6c.4.4.4 1 0 1.4L4.9 6.1a9 9 0 0 0 5 5L11 10c.4-.4 1-.4 1.4 0l2.4 2.4c.4.4.4 1 0 1.4l-1.3 1.3c-.8.8-2.2.9-3.5.3A16 16 0 0 1 .6 5.8C0 4.6.1 3.2.9 2.4l1.3-1.3c.4-.3 1-.3 1.4.1Z"/></svg>
        555 204 7719
      </li>
      <li>
        <svg viewBox="0 0 16 16" aria-hidden="true"><path d="M1 3h14v10H1z M1.5 3.5 8 9l6.5-5.5" stroke="#f1f1f1" stroke-width="1.2"/></svg>
        daniel@harborshelter.org
      </li>
      <li>
        <svg viewBox="0 0 16 16" aria-hidden="true"><circle cx="8" cy="8" r="7"/><path d="M1 8h14M8 1c2.5 2 2.5 12 0 14M8 1c-2.5 2-2.5 12 0 14" fill="none" stroke="#f1f1f1" stroke-width="1"/></svg>
        www.harborshelter.org
      </li>
    </ul>

    <div class="name-band">
      <svg viewBox="0 0 240 64" width="240" height="64" aria-hidden="true">
        <polygon points="0,64 40,0 240,0 240,64" fill="var(--brand-teal)"/>
      </svg>
      <div class="person">
        <span class="person-name">DANIEL REYES</span>
        <span class="person-title">CEO/FOUNDER</span>
      </div>
    </div>
  </section>
</main>
</body>
</html>
```